Bold Flyer Needed for Bold Little Gym

We need a 1 page flyer created for our small boutique fitness facility, CorVanto, which highlights a new service we are offering.
We are now offering Red Light Therapy (RLT) to our members and I need a full color, 1 page flyer created that captures the eye of our members while highlighting the benefits and clearly stating the prices at the bottom of the page.
Flyer will be printed out on a standard 8.5" x 11" sheet of paper and should be laid out in a way that is easy to read. Landscape or Portrait layouts are both expectable.
We are using Silverline Glow Therapy Lights LumaCore 700 Lamps as found here http://lnk.example/7QWRT5Z
I have attached the text that should be included and our logo for branding of the flyer.
Thank you!

```html
<!DOCTYPE html>
<html lang="en">
<head>
<meta charset="utf-8">
<title>CorVanto – Red Light Therapy</title>
<link href="https://fonts.googleapis.com/css2?family=Poppins:wght@400;500;600;700&display=swap" rel="stylesheet">
<style>
  :root {
    --black: #000000;
    --yellow: #f8d000;
    --white: #ffffff;
    --photo-dark: #1c1c1c;
    --photo-light: #8a8a8a;
  }
  * { margin: 0; padding: 0; box-sizing: border-box; }
  html, body { width: 848px; height: 1200px; overflow: hidden; background: var(--black); }
  body { font-family: "Poppins", sans-serif; color: var(--white); }
  .flyer { position: relative; width: 848px; height: 1200px; overflow: hidden; background: var(--black); }
  .backdrop { position: absolute; left: 0; top: 0; }
  .abs { position: absolute; }

  .brand { left: 622px; top: 24px; font-weight: 700; font-size: 34px; color: var(--yellow); letter-spacing: -0.5px; line-height: 1; }

  .intro-list { left: 63px; top: 22px; width: 560px; list-style: none; }
  .intro-list li { position: relative; padding-left: 39px; font-weight: 600; font-size: 22px; line-height: 24px; text-transform: uppercase; margin-bottom: 22px; }
  .intro-list li:nth-child(2) { margin-bottom: 22px; }
  .tick { position: absolute; left: 0; top: 3px; width: 18px; height: 18px; }

  .section-title { font-weight: 600; font-size: 23px; line-height: 26px; text-transform: uppercase; text-decoration: underline; text-decoration-color: var(--yellow); text-decoration-thickness: 2px; text-underline-offset: 3px; letter-spacing: -0.3px; }
  .what-title { left: 0; width: 848px; top: 260px; text-align: center; }
  .what-text { left: 150px; top: 303px; width: 548px; text-align: center; font-size: 11.4px; line-height: 17px; }

  .panel { left: 531px; top: 382px; width: 86px; height: 293px; border-radius: 2px;
    background: linear-gradient(90deg, #e7e1e1 0%, #f2c6c6 40%, #e9b0b0 80%, #cfcfcf 86%, #bdbdbd 100%); }

  .benefits-title { left: 63px; top: 612px; }
  .why-title { left: 63px; top: 913px; }
  .bullets { left: 63px; width: 360px; list-style: none; font-size: 11px; line-height: 15px; }
  .bullets li { position: relative; padding-left: 17px; margin-bottom: 4px; }
  .bullets li::before { content: "•"; position: absolute; left: 0; top: 0; font-size: 9px; }
  .bullets strong { color: var(--yellow); font-weight: 600; }
  .benefits-list { top: 682px; }
  .benefits-list li { margin-bottom: 4.5px; }
  .why-list { top: 958px; }
  .why-list li { margin-bottom: 9px; }

  .offer { left: 433px; width: 360px; }
  .offer-head { position: relative; padding-left: 28px; font-weight: 500; font-size: 15px; line-height: 18px; text-transform: uppercase; }
  .offer-head .tick { top: 0; width: 13px; height: 13px; }
  .offer-note { padding-left: 28px; font-size: 11px; line-height: 19px; margin-top: 5px; }
  .offer-note strong { color: var(--yellow); font-weight: 600; }
  .o1 { top: 709px; } .o2 { top: 747px; } .o3 { top: 808px; } .o4 { top: 889px; }

  .tagline { left: 433px; top: 977px; width: 400px; font-weight: 600; font-size: 26.5px; line-height: 37px; text-transform: uppercase; letter-spacing: -0.3px; }

  .price-band { left: 0; top: 1100px; }
  .tier { left: 63px; width: 135px; height: 32px; background: var(--black); color: var(--yellow); font-weight: 600; font-size: 12px; display: flex; align-items: center; justify-content: center; }
  .tier.member { top: 1115px; } .tier.non { top: 1153px; }
  .price-row { left: 198px; width: 600px; height: 32px; display: flex; align-items: center; color: var(--black); font-weight: 600; font-size: 11px; }
  .price-row.member { top: 1115px; } .price-row.non { top: 1153px; }
  .price-row span { width: 118px; padding-left: 25px; border-right: 1px solid rgba(0,0,0,0.35); line-height: 22px; }
  .price-row span:first-child { width: 146px; }
  .price-row span:last-child { border-right: none; }
</style>
</head>
<body>
<main class="flyer">
  <svg class="backdrop" width="848" height="1200" viewBox="0 0 848 1200" aria-hidden="true">
    <defs>
      <linearGradient id="photoTone" x1="0" y1="0" x2="0.3" y2="1">
        <stop offset="0" stop-color="#5a5a5a"/>
        <stop offset="0.5" stop-color="#3a3a3a"/>
        <stop offset="1" stop-color="#141414"/>
      </linearGradient>
    </defs>
    <polygon points="490,0 848,198 848,0" fill="var(--black)"/>
    <polygon points="0,272 397,536 848,269 848,530 666,410 395,571 0,303" fill="var(--yellow)"/>
    <polygon points="0,1100 677,1100 848,1198 848,1200 0,1200" fill="var(--yellow)"/>
  </svg>
  <svg class="abs" style="left:0;top:0" width="848" height="540" viewBox="0 0 848 540" role="img" aria-label="Black and white photo of a relaxed woman lying beneath a red light therapy panel">
    <polygon points="0,0 490,0 848,198 848,269 397,536 0,272" fill="url(#photoTone)"/>
  </svg>

  <div class="abs brand">CorVanto</div>

  <ul class="abs intro-list">
    <li><svg class="tick" viewBox="0 0 20 20"><circle cx="10" cy="10" r="10" fill="var(--yellow)"/><path d="M5.5 10.3l3 3 6-6.3" fill="none" stroke="var(--black)" stroke-width="2.4"/></svg>Unlock your potential with red light therapy at CorVanto!</li>
    <li><svg class="tick" viewBox="0 0 20 20"><circle cx="10" cy="10" r="10" fill="var(--yellow)"/><path d="M5.5 10.3l3 3 6-6.3" fill="none" stroke="var(--black)" stroke-width="2.4"/></svg>Introducing our new red light therapy room!</li>
    <li><svg class="tick" viewBox="0 0 20 20"><circle cx="10" cy="10" r="10" fill="var(--yellow)"/><path d="M5.5 10.3l3 3 6-6.3" fill="none" stroke="var(--black)" stroke-width="2.4"/></svg>Transform your wellness routine with the power of light!</li>
  </ul>

  <h2 class="abs section-title what-title">What is Red Light Therapy?</h2>
  <p class="abs what-text">Red Light Therapy (RLT) is a revolutionary treatment that uses specific wavelengths of light to promote healing, reduce inflammation, and enhance overall well-being. At CorVanto, we are excited to offer the advanced Silverline Glow Therapy LumaCore 700 panels—designed to maximize your health benefits in a relaxing environment.</p>

  <div class="abs panel" role="img" aria-label="Product photo of a tall red LED light therapy panel"></div>

  <h2 class="abs section-title benefits-title">Benefits of Red Light<br>Therapy</h2>
  <ul class="abs bullets benefits-list">
    <li><strong>Boosts Energy Levels:</strong> Feel revitalized and more energetic after each session.</li>
    <li><strong>Enhances Muscle Recovery:</strong> Speed up recovery times post-workout and reduce soreness.</li>
    <li><strong>Improves Skin Health:</strong> Reduce wrinkles, blemishes, and promote a youthful glow.</li>
    <li><strong>Supports Joint Health:</strong> Alleviate pain and inflammation, making movement easier.</li>
    <li><strong>Promotes Better Sleep:</strong> Improve your sleep patterns and overall restfulness.</li>
    <li><strong>Increases Circulation:</strong> Enhance blood flow for better nutrient delivery to muscles.</li>
  </ul>

  <h2 class="abs section-title why-title">Why Choose CorVanto?</h2>
  <ul class="abs bullets why-list">
    <li><strong>State-of-the-Art Equipment:</strong> Experience the power of eight Silverline Glow Therapy LumaCore 700 panels—some of the best on the market!</li>
    <li><strong>Expert Guidance:</strong> Our trained staff will guide you through each session to ensure you get the most out of your therapy.</li>
    <li><strong>Community Focused:</strong> Join a supportive community that prioritizes health and wellness.</li>
  </ul>

  <div class="abs offer o1"><div class="offer-head"><svg class="tick" viewBox="0 0 20 20"><circle cx="10" cy="10" r="10" fill="var(--yellow)"/><path d="M5.5 10.3l3 3 6-6.3" fill="none" stroke="var(--black)" stroke-width="2.4"/></svg>Special introductory offer!</div></div>
  <div class="abs offer o2"><div class="offer-head"><svg class="tick" viewBox="0 0 20 20"><circle cx="10" cy="10" r="10" fill="var(--yellow)"/><path d="M5.5 10.3l3 3 6-6.3" fill="none" stroke="var(--black)" stroke-width="2.4"/></svg>Try your first session for just $25!</div><p class="offer-note">(Regularly $55)</p></div>
  <div class="abs offer o3"><div class="offer-head"><svg class="tick" viewBox="0 0 20 20"><circle cx="10" cy="10" r="10" fill="var(--yellow)"/><path d="M5.5 10.3l3 3 6-6.3" fill="none" stroke="var(--black)" stroke-width="2.4"/></svg>Limited time only!</div><p class="offer-note">Book your session today and discover how Red Light Therapy can elevate your fitness journey.</p></div>
  <div class="abs offer o4"><div class="offer-head"><svg class="tick" viewBox="0 0 20 20"><circle cx="10" cy="10" r="10" fill="var(--yellow)"/><path d="M5.5 10.3l3 3 6-6.3" fill="none" stroke="var(--black)" stroke-width="2.4"/></svg>Ready to shine?</div><p class="offer-note">Visit our front desk or call us at <strong>(555) 214- 3380</strong> to schedule your appointment.</p></div>

  <p class="abs tagline">CorVanto Fitness Facility, Your Wellness, Our Commitment!</p>

  <div class="abs tier member">CORVANTO MEMBER</div>
  <div class="abs tier non">NON-MEMBER</div>
  <div class="abs price-row member"><span>$35/Single Session</span><span>$102/3 – Pack</span><span>$167/5 – Pack</span><span>$316/10 – Pack</span></div>
  <div class="abs price-row non"><span>$55/Single Session</span><span>$159/3 – Pack</span><span>$259/5 – Pack</span><span>$491/10 – Pack</span></div>
</main>
</body>
</html>
```